Medical Learning Web Design Project

The web site will be a site for medical students. It is aimed at providing a collaborative place for students to study, learn, question each other and challenge each other with learning. The site needs to have a section on the page that is for the content and this needs to be relatively clean and clinical. The surrounding elements will be informative (for the statistics, challenge etc). There will also be a slide-out screen that allows for the social/friend elements of the site.

The colour scheme needs to be clean and clinical where appropriate, but also engaging and exciting for the social/competitive elements.
Updates

Just for clarity: The site isn't expected to be 'coded' ... it is just the layered PSD files that I need.

Also, with regards to the navigation buttons ... they will never ALL be present at the same time so don't feel the need to design all on one page, but creativity around allowing few or many on a page will be an advantage ...

Thanks

Hi,

Please note that the image uploaded has been done as a wireframe by the developers. I am looking for a more creative and engaging way of presenting that content ...

Thanks

Hi all

Thank you all for the designs so far ...!

Please have a look at the new uploaded file, I am also looking not just for a 'templated home page' but also some different layouts that are represented in these wireframes. If the various layouts represented can be condensed down into 1 or 2 page templates with appropriate colour schemes to capture the type of content on the page (as already mentioned ... social .. competitive ... learning), then that will help me live the concepts better too! The friends tab for instance I have envisaged as a slider covering the screen and then sliding back when complete ... but let me see what creativity you can give to this ...!

Many thanks

Reason: Just allowing for final tweaks ...

Target Market(s)

Medical Students

Industry/Entity Type

Medical

Requirements
Must have
• - Not cluttered appearance
- Dynamic navigation (ie. site will be developed to only show relevant navigation buttons on each page ...)
- Navigation buttons (need to be individual buttons) will be: 'Home', 'Take the tour', 'What your peers say', 'Subscriptions', 'Free Signup', 'Contact us', 'Moderation', 'Statistics', 'Competition', 'Answer Questions', 'Post Questions', 'My profile', 'Friends'
- Please also ensure it is engaging for social elements and competitive elements (perhaps slightly different design for pages focussed on each element)
- Please also ensure that there is a masculine design and feminine design that has continuity for the site but depending on gender the design can be tailored to be more appealing (that means perhaps male social design, male competitive design, female social design, female competitive design ... without loosing continuity through the site).
- Photoshop PSD format
- Pixel perfect at least 1000 pixels wide (but the design needs to allow for various monitor sizes (only desktop or laptops ... not tablets or smart phones)

```html
<!DOCTYPE html>
<html lang="en">
<head>
<meta charset="utf-8">
<title>Medora – The Medical Peer Review</title>
<link href="https://fonts.googleapis.com/css2?family=Ubuntu:wght@400;500&family=Delius&display=swap" rel="stylesheet">
<style>
:root{
  --teal-dark:#2c6c77;
  --teal-mid:#3f8589;
  --teal-nav:#2f7380;
  --teal-head:#2a6670;
  --sky-top:#c7e7ee;
  --sky-bottom:#8fcbd7;
  --paper:#f0f2f2;
  --text-grey:#8a8f90;
  --line:#dfe3e3;
  --white:#ffffff;
  --link:#4aa5c0;
}
*{margin:0;padding:0;box-sizing:border-box}
html,body{width:1200px;height:1200px;overflow:hidden}
body{position:relative;font-family:Arial,Helvetica,sans-serif;background:var(--paper);color:var(--text-grey)}
.abs{position:absolute}
h2,h3,.ubuntu{font-family:"Ubuntu",sans-serif;font-weight:400;color:var(--teal-head)}

/* header */
.site-header{left:0;top:0;width:1200px;height:96px;background:linear-gradient(180deg,var(--sky-top),var(--sky-bottom))}
.brand{left:198px;top:34px;color:var(--white);font-family:"Ubuntu",sans-serif;font-size:34px;line-height:1}
.brand-tag{left:200px;top:71px;font-size:10px;color:var(--white)}
.util{top:0;font-size:9px;height:15px;line-height:15px;padding:0 5px}
.util-contact{left:906px;color:var(--teal-nav)}
.util-login{left:958px;background:var(--teal-nav);color:var(--white);border-radius:0 0 3px 3px}
.quote{left:520px;top:32px;width:391px;text-align:right;font-size:10px;color:var(--white);line-height:14px}
.stats-line{left:562px;top:66px;font-family:"Ubuntu",sans-serif;font-size:15px;color:#4b8a96}

/* navigation */
.main-nav{left:0;top:96px;width:1200px;height:28px;background:var(--teal-nav);border-top:1px solid #5d9fa9}
.main-nav ul{list-style:none;position:absolute;right:208px;top:0;display:flex;height:28px;align-items:center}
.main-nav li{font-size:10px;color:#d9eef1;padding:0 9px;border-left:1px solid #3f8590;display:flex;align-items:center;gap:5px}
.main-nav li:first-child{border-left:none;color:var(--white);font-size:11px}
.main-nav svg{width:12px;height:12px}

/* hero */
.hero{left:0;top:124px;width:1200px;height:360px;background:linear-gradient(180deg,#5aa6b3 0%,#4f9dab 60%,#3f8797 61%,#5ba7b6 100%)}
.slider{left:200px;top:141px;width:800px;height:307px;border:5px solid var(--white);background:radial-gradient(ellipse at 30% 40%,#4a9095,#357a7e)}
.slider-shadow{left:280px;top:448px;width:640px;height:22px;border-radius:50%;background:radial-gradient(ellipse,rgba(20,50,60,.55),rgba(20,50,60,0) 70%)}
.slide-title{left:230px;top:186px;font-family:"Delius",cursive;font-size:19px;color:var(--white)}
.slide-list{left:230px;top:218px;list-style:none;font-family:"Delius",cursive;font-size:11.5px;color:#eaf6f6;line-height:19.2px}
.slide-list li::before{content:"• ";font-size:9px}
.slide-photo{left:579px;top:161px;width:400px;height:266px;background:linear-gradient(135deg,#eef3f4,#d6e3e5 60%,#c7d8db)}
.slide-arrow{top:282px;width:19px;height:24px;background:#e6eded;display:flex;align-items:center;justify-content:center}
.slide-arrow.left{left:205px;border-radius:0 3px 3px 0}
.slide-arrow.right{left:977px;border-radius:3px 0 0 3px}

/* notifications */
.notice-bar{left:0;top:484px;width:1200px;height:30px;background:#4a8e98}
.notice-label{left:0;top:484px;width:296px;height:30px;background:var(--teal-dark);color:var(--white);font-size:10px;line-height:30px;padding-left:199px}
.notice-chevron{left:296px;top:484px;width:0;height:0;border-top:15px solid transparent;border-bottom:15px solid transparent;border-left:8px solid var(--teal-dark)}
.notice-text{left:329px;top:484px;line-height:30px;font-size:8.5px;color:#e0f0f2}
.notice-text u{color:var(--white)}
.social-strip{left:848px;top:484px;width:152px;height:30px;background:#3b7f89;display:flex;gap:4.5px;align-items:center;padding-left:7px}
.social-strip span{width:20px;height:20px;border-radius:3px}

/* content */
.section-title{font-size:22px}
.copy{font-size:9.6px;line-height:14.4px}
.welcome-title{left:200px;top:532px}
.welcome-copy{left:200px;top:566px;width:428px}
.welcome-copy p+p{margin-top:14.4px}
.btn-read{left:547px;top:677px;width:80px;height:22px;background:var(--teal-dark);color:var(--white);font-size:9.5px;text-align:center;line-height:22px;border-radius:2px}
.works-title{left:656px;top:532px}
.video{left:657px;top:570px;width:343px;height:128px;background:#7ea5a8;display:flex;align-items:center;justify-content:center}
.divider{left:200px;top:723px;width:800px;height:1px;background:var(--line)}
.col-title{top:745px;font-size:15.5px}
.card{top:776px;background:var(--white);border:1px solid var(--line)}
.testimonial{left:200px;width:291px;height:177px;padding:23px 13px 0;font-size:8.2px;line-height:12.8px;text-align:justify}
.testimonial p+p{margin-top:12.8px}
.bubble-tail{left:405px;top:952px;width:0;height:0;border-left:26px solid transparent;border-top:20px solid var(--white)}
.author{left:330px;top:972px;width:161px;text-align:right;font-size:8.8px;line-height:10px;color:#b0b4b5}
.author b{color:#8f9494;font-size:10px}
.like-box{left:521px;width:224px;height:228px}
.like-icon{left:9px;top:9px;width:30px;height:30px;border-radius:3px;background:#5b7cc0}
.like-name{left:48px;top:9px;font-size:11.5px;font-weight:bold;color:#3b5998}
.like-btn{left:48px;top:27px;width:38px;height:17px;border:1px solid #cad4e7;background:#eef2f9;font-size:8px;color:#3b5998;line-height:15px;text-align:center;border-radius:2px}
.like-feed{left:3px;top:51px;width:216px;height:157px;border-top:1px solid var(--line)}
.like-scroll{right:0;top:0;width:11px;height:157px;background:#f3f3f3;border-left:1px solid var(--line)}
.like-foot{left:7px;top:211px;font-size:7px;color:#666;display:flex;align-items:center;gap:5px}
.like-foot span{width:10px;height:10px;background:#3b5998;display:inline-block}
.follow-box{left:774px;width:226px;height:228px;overflow:hidden;padding:0 7px}
.tweet{display:flex;gap:8px;padding:7px 0;border-bottom:1px dotted #d4d9d9;height:64px}
.tweet svg{flex:none;margin-top:7px}
.tweet p{font-size:9.5px;line-height:12px;color:#8a8f90}
.tweet a{display:block;font-size:8px;color:var(--link);text-decoration:none;line-height:11px}
.tweet small{font-size:8px;color:#b5b9b9}

/* footer */
.site-footer{left:0;top:1028px;width:1200px;height:172px;background:linear-gradient(180deg,#2f727c,#2a6870)}
.foot-title{color:var(--white);font-size:18px;top:1042px}
.foot-links{list-style:none;font-size:9.8px;line-height:16.8px;color:#c3dde0;top:1072px}
.foot-links li::before{content:"» "}
.contact-block{left:467px;top:1072px;font-size:9.8px;line-height:14.4px;color:#c3dde0}
.contact-strong{left:467px;top:1135px;font-family:"Ubuntu",sans-serif;font-size:10px;line-height:16px;color:var(--white)}
.news-copy{left:620px;top:1073px;width:380px;font-size:8.2px;line-height:10.5px;color:#c3dde0}
.news-input{left:622px;top:1108px;width:287px;height:29px;background:#eaf3f4;border:1px solid #a8cdd2;border-radius:2px;font-size:9.5px;color:#a9b6b8;line-height:27px;padding-left:10px}
.news-join{left:914px;top:1108px;width:86px;height:29px;background:linear-gradient(180deg,#4d8f98,#2d6a72);border-radius:3px;color:var(--white);font-size:11px;text-align:center;line-height:29px}
.copyright-mark{left:620px;top:1151px;width:11px;height:11px;border:1.5px solid var(--white);border-radius:50%}
.copyright{left:620px;top:1174px;font-size:9.8px;color:#c3dde0}
</style>
</head>
<body>

<header class="abs site-header">
</header>
<div class="abs brand">Medora</div>
<div class="abs brand-tag">The Medical Peer Review</div>
<div class="abs util util-contact">Contact</div>
<div class="abs util util-login">&#10150; Login</div>
<div class="abs quote">“ Medora keeps me ahead of the game, constantly testing my knowledge... ”<br>Tom. Doctor in training Northfield University</div>
<div class="abs stats-line">How will your stats compare?</div>

<nav class="abs main-nav">
  <ul>
    <li><svg viewBox="0 0 12 12"><path d="M1 6 6 1.5 11 6H9.5v5H7V8H5v3H2.5V6z" fill="#fff"/></svg>Home</li>
    <li><svg viewBox="0 0 12 12"><circle cx="6" cy="6" r="4.5" fill="none" stroke="#fff" stroke-width="1.6"/></svg>Take the Tour</li>
    <li><svg viewBox="0 0 12 12"><rect x="1" y="3" width="10" height="6" rx="1" fill="#e4f1f3"/></svg>What your Peers Say</li>
    <li><svg viewBox="0 0 12 12"><path d="M3 1h4.5L9.5 3v8H3z" fill="#e4f1f3"/></svg>Subscription Plans</li>
    <li><svg viewBox="0 0 12 12"><rect x="1.5" y="2.5" width="8" height="8" fill="none" stroke="#fff"/><path d="M5 7 10.5 1.5" stroke="#fff" stroke-width="1.4"/></svg>Free Signup</li>
  </ul>
</nav>

<section class="abs hero"></section>
<div class="abs slider-shadow"></div>
<div class="abs slider"></div>
<h3 class="abs slide-title">Lorem Ipsum is simply dummy text</h3>
<ul class="abs slide-list">
  <li>Suspendisse luctus orci ac nisl ultricies quis.</li>
  <li>Integer euismod enim in quam molestie varius.</li>
  <li>Sed pellentesque odio in eros aliquam gravida.</li>
  <li>Curabitur volutpat mi nec metus fermentum congue.</li>
  <li>Phasellus eget dolor ut turpis luctus laoreet.</li>
  <li>Cras eget dolor a odio tempus sollicitudin.</li>
  <li>Quisque eu mi nunc, eget porttitor augue.</li>
  <li>Fusce sollicitudin adipiscing tellus, sit amet.</li>
  <li>Fusce sit amet odio tellus, eu gravida nibh.</li>
</ul>
<div class="abs slide-photo" role="img" aria-label="Photo of a smiling medical student in a lab coat working with test tubes in a bright laboratory"></div>
<div class="abs slide-arrow left"><svg width="8" height="10" viewBox="0 0 8 10"><path d="M2 1l4 4-4 4" stroke="#7d9a9c" stroke-width="2" fill="none"/></svg></div>
<div class="abs slide-arrow right"><svg width="8" height="10" viewBox="0 0 8 10"><path d="M6 1 2 5l4 4" stroke="#7d9a9c" stroke-width="2" fill="none"/></svg></div>

<div class="abs notice-bar"></div>
<div class="abs notice-label">NOTIFICATIONS</div>
<div class="abs notice-chevron"></div>
<div class="abs notice-text">Medora is now on our social page. Follow us here <u>social.example/medora</u></div>
<div class="abs social-strip">
  <span style="background:#49a33b"></span>
  <span style="background:#c4302b"></span>
  <span style="background:#d32323"></span>
  <span style="background:#2c79b0"></span>
  <span style="background:#4fb6de"></span>
  <span style="background:#3b5998"></span>
</div>

<h2 class="abs section-title welcome-title">Welcome to Medora</h2>
<div class="abs copy welcome-copy">
  <p>Lorem Ipsum is simply dummy text of the printing and typesetting industry. Lorem Ipsum has been the industry's standard dummy text ever since the 1500s, when an unknown printer took a galley of type and scrambled it to make a type specimen book.</p>
  <p>It has survived not only five centuries, but also the leap into electronic typesetting, remaining essentially unchanged. It was popularised in the 1960s with the release of Typesheet sheets containing Lorem Ipsum passages, and more recently with desktop publishing software like LayoutPro including versions of Lorem Ipsum.</p>
</div>
<div class="abs btn-read">read more</div>

<h2 class="abs section-title works-title">How Medora works?</h2>
<div class="abs video" role="img" aria-label="Video player explaining how the site works">
  <svg width="24" height="30" viewBox="0 0 24 30"><path d="M1 1l22 14L1 29z" fill="#fff"/></svg>
</div>

<div class="abs divider"></div>

<h3 class="abs col-title" style="left:200px">Testimonials</h3>
<div class="abs card testimonial">
  <p>Lorem Ipsum is simply dummy text of the printing and typesetting industry. Lorem Ipsum has been the industry's standard dummy text ever since the 1500s, when an unknown printer took a galley of type and scrambled it to make a type specimen book.</p>
  <p>It has survived not only five centuries, but also the leap into electronic typesetting, remaining essentially unchanged. It was popularised in the 1960s with the release of Typesheet sheets containing Lorem Ipsum passages, and more recently with desktop publishing software like LayoutPro including versions.</p>
</div>
<div class="abs bubble-tail"></div>
<div class="abs author"><b>John Doe</b><br>Doctor<br>Northfield University</div>

<h3 class="abs col-title" style="left:521px">Like Us</h3>
<div class="abs card like-box">
  <div class="abs like-icon"></div>
  <div class="abs like-name">Dev Community</div>
  <div class="abs like-btn">Like</div>
  <div class="abs like-feed"><div class="abs like-scroll"></div></div>
  <div class="abs like-foot"><span></span>Social plugin</div>
</div>

<h3 class="abs col-title" style="left:774px">Follow Us</h3>
<div class="abs card follow-box">
  <div class="tweet"><svg width="26" height="18" viewBox="0 0 26 18"><ellipse cx="13" cy="10" rx="11" ry="7" fill="#7fc2db"/></svg><p>Sed mollis eros ut erat condimentum of form congue risus vehicula.<a>http://www.feedsample.net/medora</a><small>20 mins ago</small></p></div>
  <div class="tweet"><svg width="26" height="18" viewBox="0 0 26 18"><ellipse cx="13" cy="10" rx="11" ry="7" fill="#7fc2db"/></svg><p>Sed mollis eros ut erat condimentum of form congue risus vehicula.<a>http://www.feedsample.net/medora</a><small>20 mins ago</small></p></div>
  <div class="tweet"><svg width="26" height="18" viewBox="0 0 26 18"><ellipse cx="13" cy="10" rx="11" ry="7" fill="#7fc2db"/></svg><p>Sed mollis eros ut erat condimentum of form congue risus vehicula.<a>http://www.feedsample.net/medora</a><small>20 mins ago</small></p></div>
  <div class="tweet" style="border:none"><svg width="26" height="18" viewBox="0 0 26 18"><ellipse cx="13" cy="10" rx="11" ry="7" fill="#7fc2db"/></svg><p>Sed mollis eros ut erat condimentum of form congue risus vehicula.</p></div>
</div>

<footer class="abs site-footer"></footer>
<h3 class="abs foot-title" style="left:200px">Sitemap</h3>
<ul class="abs foot-links" style="left:200px">
  <li>Home</li><li>Take the Tour</li><li>What Your Peers Say</li><li>Subscription Plans</li><li>Free Signup</li><li>Contact Us</li><li>Lorem Ipsum</li>
</ul>
<ul class="abs foot-links" style="left:326px">
  <li>Established</li><li>Take the Tour</li><li>What Your Peers Say</li><li>Subscription Plans</li><li>Free Signup</li><li>Contact Us</li><li>Sitemap</li>
</ul>
<h3 class="abs foot-title" style="left:467px">Contact Us</h3>
<div class="abs contact-block">Medora Limited<br>Street Name<br>Lorem Ipsum is simply<br>Country Name</div>
<div class="abs contact-strong">Phone: 001 555 0142<br>Email: info@medora-mail.com</div>
<h3 class="abs foot-title" style="left:620px">Newsletter</h3>
<div class="abs news-copy">Join our Newsletter today Sed ut perspiciatis unde omnis iste natus error sit voluptatem accusanti doloremque laudantium, totam rem aperiam, eaque ipsa quae.</div>
<div class="abs news-input">Email</div>
<div class="abs news-join">Join</div>
<div class="abs copyright-mark"></div>
<div class="abs copyright">Copyright 2012 Medora Limited</div>

</body>
</html>
```